Product packaging design for lentils

Looking to create a design for lentils in 4lb format. We are looking to create a base design for the bags, and then from there will have additional designs for the different products with different product name, barcodes and nutritional information.

Industry/Entity Type

Food

```html
<!DOCTYPE html>
<html lang="en">
<head>
<meta charset="utf-8">
<title>Grainvale Lentils – Pouch Front</title>
<link rel="stylesheet" href="https://fonts.googleapis.com/css2?family=Questrial&family=Mulish:wght@400;700&display=swap">
<style>
  :root {
    --stage: #cfcfcf;
    --pouch-top: #2b2b2b;
    --pouch-mid: #141414;
    --pouch-bottom: #050505;
    --brand-green: #7cb342;
    --dot-green: #8bc34a;
    --dot-pale: #dff0cc;
    --lentil-deep: #a9552f;
    --lentil-mid: #c77a4f;
    --lentil-light: #e0a37c;
    --text-light: #f2f2f2;
    --text-muted: #9a9a9a;
  }
  * { margin: 0; padding: 0; box-sizing: border-box; }
  html, body {
    width: 1200px; height: 800px; overflow: hidden;
    background: var(--stage);
  }
  .canvas {
    position: relative; width: 1200px; height: 800px;
    background: var(--stage);
  }
  .pouch-front {
    position: absolute; left: 360px; top: 30px;
    width: 480px; height: 740px;
    border-radius: 6px 6px 10px 10px;
    background: linear-gradient(180deg, var(--pouch-top) 0%, var(--pouch-mid) 45%, var(--pouch-bottom) 100%);
    overflow: hidden;
  }
  .dot-column {
    position: absolute; left: 67px; top: 0;
    width: 132px; height: 405px;
    background: linear-gradient(90deg, var(--dot-pale) 0%, var(--dot-green) 70%);
    opacity: 0.55;
  }
  .brand-lockup {
    position: absolute; left: 280px; top: 258px;
    display: flex; align-items: center; gap: 8px;
  }
  .brand-dot {
    width: 18px; height: 18px; border-radius: 50%;
    background: var(--brand-green);
  }
  .brand-name {
    font-family: "Questrial", sans-serif;
    font-size: 24px; color: var(--brand-green);
  }
  .product-name {
    position: absolute; right: 78px; top: 318px;
    font-family: "Questrial", sans-serif;
    font-size: 56px; line-height: 1;
    color: var(--text-light);
    letter-spacing: -1px;
    padding-bottom: 4px;
    border-bottom: 3px solid var(--brand-green);
  }
  .lentil-window {
    position: absolute; left: 0; top: 407px;
    width: 480px; height: 163px;
    background: linear-gradient(110deg, var(--lentil-light) 0%, var(--lentil-mid) 35%, var(--lentil-deep) 100%);
  }
  .product-copy {
    position: absolute; left: 62px; top: 598px; width: 340px;
    font-family: "Mulish", sans-serif;
    font-size: 5.5px; line-height: 1.35;
    color: var(--text-muted);
  }
  .benefit-row {
    position: absolute; left: 62px; top: 648px; width: 340px;
    display: flex; align-items: center; justify-content: space-between;
    font-family: "Mulish", sans-serif; font-size: 8.5px;
    color: var(--text-muted);
  }
  .benefit { display: flex; align-items: center; gap: 3px; }
  .benefit svg { width: 18px; height: 18px; }
  .benefit-sep { width: 2px; height: 5px; background: var(--text-light); }
  .net-weight {
    position: absolute; right: 88px; top: 686px;
    font-family: "Mulish", sans-serif; font-weight: 700;
    font-size: 12px; color: var(--text-muted);
  }
</style>
</head>
<body>
<main class="canvas">
  <section class="pouch-front">
    <div class="dot-column" role="img" aria-label="Decorative column of green dots fading to pale green"></div>

    <div class="brand-lockup">
      <span class="brand-dot"></span>
      <span class="brand-name">Grainvale</span>
    </div>

    <h1 class="product-name">lentils</h1>

    <div class="lentil-window" role="img" aria-label="Photo of red lentils seen through the clear window"></div>

    <p class="product-copy">Lorem ipsum dolor sit amet, consectetur adipiscing elit, sed do eiusmod tempor incididunt ut labore et dolore magna aliqua. Tempor id eu nisl nunc mi ipsum faucibus vitae aliquet. Elit sed vulputate mi sit. Neque eu nisi egestas congue quisque egestas. Arcu dictum varius duis at consectetur. Facilisis mauris conse faucibus vitae sit amet massa eiusmod tempor vitae tortor condimentum lacinia quis. Nunc mi eu nisl nunc mi ipsum faucibus.</p>

    <div class="benefit-row">
      <span class="benefit">
        <svg viewBox="0 0 20 20"><circle cx="10" cy="10" r="7" fill="none" stroke="var(--brand-green)" stroke-width="1.4"/></svg>
        FRESH
      </span>
      <span class="benefit-sep"></span>
      <span class="benefit">
        <svg viewBox="0 0 20 20"><path d="M10 18V4" stroke="var(--brand-green)" stroke-width="1.2" fill="none"/></svg>
        High Fiber
      </span>
      <span class="benefit-sep"></span>
      <span class="benefit">
        <svg viewBox="0 0 20 20"><path d="M10 2C7 7 5 10 5 13a5 5 0 0 0 10 0c0-3-2-6-5-11z" fill="none" stroke="var(--brand-green)" stroke-width="1.2"/></svg>
        Low Fat
      </span>
      <span class="benefit-sep"></span>
      <span class="benefit">
        <svg viewBox="0 0 20 20"><path d="M10 17 3 10a4 4 0 0 1 7-5 4 4 0 0 1 7 5z" fill="none" stroke="var(--brand-green)" stroke-width="1.2"/><path d="M7 10l2 2 4-4" fill="none" stroke="var(--brand-green)" stroke-width="1.2"/></svg>
        Heart Health
      </span>
    </div>

    <p class="net-weight">15g</p>
  </section>
</main>
</body>
</html>
```